Commercial Real Estate Corporate Site

Our company sells an ERP software to Commercial Real Estate Companies, this project is part of a marketing and sales relaunch of the company.

See attached for PDF formatted Design brief

The software is a modular system where client’s can adopt one module at a time. Our customers are corporate clients who own between 10M and 10B of real estate properties. The typical customer is from the IT or the Financial arm of the company. Our differentiation in the market is that our system is built on a no-code environment, so making changes for the client is quick. Incumbents in the market have long implementation cycles, and customization is often not possible. Competitors are Quorvel, TKB, PlotNest, Vumora.

We need a design for our site which will be implemented into Brevo Forge. **All designs must be compatible with the newest version of Brevo Forge.**

We have produced the following attached assets to use in the website design.:

1. Logo
2. Brand Guidelines
3. Content for Pages
4. Menu Structures
5. Illustrations (modules)
I can't attach them because the files are too big, so they're in this google drive instead:
https://files.examplestore.net/share/k29Xa7Lq0Pz3Rt8MwB5nYc4Hv1Jd6Fe?mode=view

The mechanic for our sales process is as follows:

1. We find on module from our application that a client is interested in. The illustrations that we’ve attached represent the individual modules (elements) of the software.
1. For instance, one of our current customers has purchased a commissions module from us which helps calculate the commission that brokers receive for buying and selling their properties.
2. We provide immense value through the module, and then keep in sales communication with the client to determine which other modules we can implement for them.
1. For instance, in the example above, the client is so happy with the commissions module that they want to start working with our leasing module as well. In the next business quarter, they also choose to add our financials module to their business systems.

### Logo

Attached

### Brand Guidelines

Attached

We are open to suggestions on the secondary colour palette.

### **Site Copy**

**We require the following pages to be created; For now, we will do one Market Page, one Product Page, and one Platform / Services Page, and we will use those as inspiration to create the other dozen Marketing Pages and 30 or so Product Pages.**

**Homepage**

Attached

**Market Page** - look at the quorvel site under the Office, Industrial, Retail (https://www.quorvel.com/products/quorvel-commercial-suite/)

**Product** - One product provided, but there will be 30 - look at the vumora page

(https://www.vumora.com/products/general-accounting)

**Platform / Services Page** - pages that tell the story of our platform and services, content to be provided - the platform will use our modules as it highlights the story of the configurability and composability of the platform. Instead of the icons that they use, we want to use our modules.

- https://www.pelbrix.com/enterprise-applications-platform
- https://www.pelbrix.com/cloud-architecture

**Team Page** - just add sample content for starters (6 Team Members to start)

**Schedule Demo Page** - the call to action for all pages

(https://go.vumora.com/schedule-demo.html)

### Menu Structure

The menu is provided as an attachment.

### Illustrations Information

A note about the illustrations - we have provided an illustrator file with the modules, and if you’d like you can arrange the in any way that you’d like to. We especially like when the modules are positioned like a periodic table of the elements.

Our existing clients are

- Torvane Coop - https://www.torvanecoop.com/real-estate/
- Dalsworth Realestate https://dalsworth.com

Our competitors are

- Quorvel - www.quorvel.com
- TKB - [www.tkbsoftware.com](https://www.tkbsoftware.com/) (we don’t like how this one looks)
- Vumora - www.vumora.com
- Plotnest - www.plotnest.com

Design inspiration

- https://lark-studio.brevosite.com/velmo
- Corporate
- Established
- Modern

### Stock Images Guidance

- https://www.drafta.net/design/QXR7Lm2TpWz/Hk9vN3c8Yd41-FbqsaZRr/edit?utm_content=QXR7Lm2TpWz&utm_campaign=designshare&utm_medium=link2&utm_source=sharebutton

Target Market(s)

Commercial Real Estate Companies - they typically own a portfolio of 50 - 5000 real estate properties and need a software to manage it all.

Coding

Coded - Design and coding required

Number of Pages Required

5+ page

Font styles to use
Other font styles liked:
• Fonts defined in brand guideline

Requirements
Must have
• Brevo Forge, Use the Elemental Design, Download ai.zip and png.zip Use Brand Guideline,
Nice to have
• Check design breif

```html
<!DOCTYPE html>
<html lang="en">
<head>
<meta charset="utf-8">
<title>Orvanta – Elemental</title>
<link href="https://fonts.googleapis.com/css2?family=Montserrat:wght@500;600;700&family=Roboto:wght@400;500;700&display=swap" rel="stylesheet">
<style>
:root{
  --red:#e0070b;
  --dark:#1f1f1f;
  --slate:#4d4d4d;
  --text:#444;
  --muted:#666;
  --line:#cfcfcf;
  --white:#fff;
}
*{margin:0;padding:0;box-sizing:border-box}
html,body{width:1200px;height:3710px;overflow:hidden;background:var(--white)}
body{position:relative;font-family:'Roboto',sans-serif;color:var(--text)}
.abs{position:absolute}
.h-mont{font-family:'Montserrat',sans-serif;font-weight:600;letter-spacing:1px}
.body-copy{font-size:13px;line-height:25.7px;color:var(--text)}
.brand{font-family:'Roboto',sans-serif;font-weight:700;color:var(--red);display:flex;align-items:center;gap:10px}
.brand-square{width:34px;height:34px;background:var(--red)}

/* header */
.site-header{left:0;top:0;width:1200px;height:84px}
.site-header .brand{left:144px;top:22px;font-size:34px}
.nav{left:518px;top:31px;display:flex;gap:34px;font-size:14px;font-weight:500;color:var(--dark)}
.nav a{color:inherit;text-decoration:none}
.btn-demo{left:896px;top:17px;width:160px;height:45px;border-radius:23px;background:var(--red);color:var(--white);font-size:13px;font-weight:700;display:flex;align-items:center;justify-content:center}

.hero-title{left:0;top:110px;width:1200px;text-align:center;color:var(--white);font-size:62px}
.photo{background:linear-gradient(160deg,#7d9ac4 0%,#a8bcd6 35%,#6b7686 60%,#3a3f4a 100%)}
.hero-photo{left:144px;top:202px;width:912px;height:420px}

.welcome{left:0;top:690px;width:1200px;text-align:center;font-size:48px;color:var(--dark)}
.welcome span,.modules-title span,.about-us h2 span{color:var(--red)}
.welcome-copy{left:213px;top:770px;width:774px;text-align:center}

.about-band{left:108px;top:966px;width:700px;height:87px;background:var(--red);display:flex;align-items:center;padding-left:37px;color:var(--white)}
.about-band .h-mont{font-size:48px;margin-right:22px}
.about-band .tag{font-size:27px}
.enterprise-title{left:143px;top:1100px;font-size:34px;font-weight:700;color:var(--dark)}
.enterprise-copy{left:143px;top:1168px;width:522px;text-align:justify}

.modules-title{left:0;top:1572px;width:1200px;text-align:center;font-size:48px;line-height:60px;color:var(--dark)}
.pillar-title{font-size:34px;font-weight:500;color:var(--dark)}
.modules-head{left:587px;top:1816px}
.modules-copy{left:587px;top:1880px;width:469px;text-align:justify}

.platform-title{left:0;top:2368px;width:1200px;text-align:center;font-size:48px;color:var(--white)}
.platform-head{left:141px;top:2497px;color:var(--white)}
.platform-copy{left:141px;top:2556px;width:469px;text-align:justify;color:var(--white)}

.about-us .brand{left:188px;top:3160px;font-size:62px}
.about-us h2{left:543px;top:3122px;font-size:48px;color:var(--dark)}
.about-us p{left:543px;top:3186px;width:472px}

.rule{left:144px;width:912px;height:1px;background:var(--line)}
.site-footer .brand{left:144px;top:3456px;font-size:34px}
.foot-col h4{font-size:16px;font-weight:500;color:var(--dark);margin-bottom:6px}
.foot-col li{list-style:none;font-size:14px;line-height:25px;color:var(--muted)}
.newsletter{left:826px;top:3480px;width:232px;height:46px;border:2px solid var(--line);border-radius:23px}
.newsletter .ph{position:absolute;left:24px;top:13px;font-size:13px;color:var(--muted)}
.newsletter .sub{position:absolute;right:3px;top:3px;width:96px;height:36px;border-radius:18px;background:var(--red);color:var(--white);font-size:13px;font-weight:700;display:flex;align-items:center;justify-content:center}
.copyright{left:144px;top:3658px;font-size:14px;color:var(--muted)}
.social{left:936px;top:3662px;display:flex;gap:14px}
.social span{width:12px;height:12px;background:var(--dark);border-radius:2px}
</style>
</head>
<body>

<svg class="abs" style="left:0;top:0" width="1200" height="3710" aria-hidden="true">
  <polygon points="0,84 1200,84 1200,300 1056,370 144,330 0,300" fill="var(--red)"/>
  <polygon points="40,1955 168,1728 450,1728 450,2183 168,2183" fill="var(--red)"/>
  <polygon points="600,2183 1200,2455 1200,2895 600,3048 0,2895 0,2460" fill="var(--slate)"/>
  <polygon points="600,2183 1200,2330 1200,2455" fill="var(--red)"/>
  <polygon points="0,2770 600,3048 0,2895" fill="var(--red)"/>
</svg>

<header class="abs site-header">
  <div class="abs brand"><span class="brand-square"></span>ORVANTA</div>
  <nav class="abs nav"><a href="#">HOME</a><a href="#">MARKET</a><a href="#">PLATFORM</a><a href="#">TEAM</a></nav>
  <div class="abs btn-demo">SCHEDULE DEMO</div>
</header>

<h1 class="abs hero-title h-mont">ELEMENTAL</h1>
<div class="abs photo hero-photo" role="img" aria-label="Modern commercial office building at dusk"></div>

<h2 class="abs welcome h-mont">WELCOME TO <span>ORVANTA</span></h2>
<p class="abs body-copy welcome-copy">An infinitely composable Enterprise Applications Platform (EAP) for real estate. Far beyond what's possible with tired, legacy real estate ERP software, Orvanta offers a complete industry solution, architected as flexible modules that can be assembled and configured into an infinite combination of processes and workflows. The Orvanta Enterprise solution seamlessly delivers both modular software and bundled services to transform your business with less risk, greater security, and lower cost.</p>

<div class="abs photo" style="left:716px;top:868px;width:484px;height:680px;clip-path:polygon(60% 0,100% 8%,100% 100%,25% 100%,0 55%);background:linear-gradient(150deg,#0b1e3a,#1f6fb0 50%,#0a1a30)" role="img" aria-label="Illuminated digital city model on a circuit board"></div>
<div class="abs about-band"><span class="h-mont">ABOUT</span><span class="tag">One Solution - Infinite Possibilities</span></div>
<h3 class="abs enterprise-title">Orvanta Enterprise</h3>
<p class="abs body-copy enterprise-copy">Orvanta was born from decades of real estate enterprise software development and implementation experience — spanning hundreds of blue chip global real estate investment firms. But Orvanta is unlike anything you've experienced before. No more multi-million-dollar disruptive implementations. No more waiting for upgrades and enhancements that never come. No more trailing projects and disappointing customizations. No more settling for less than exactly what you want. You can begin using Orvanta simply — starting with a single module. Then, you can build-on with additional modules at your own pace. Orvanta Enterprise combines software and services in a simple, annual subscription.</p>

<h2 class="abs modules-title h-mont">THE MODULES OF<br><span>ORVANTA (AKA PLATFORM?)</span></h2>
<div class="abs photo" style="left:142px;top:1780px;width:420px;height:352px;clip-path:polygon(0 50%,22% 0,78% 0,100% 50%,78% 100%,22% 100%);background:linear-gradient(135deg,#f4f4f4,#e2e2e2)" role="img" aria-label="Software modules arranged like a periodic table"></div>
<h3 class="abs pillar-title modules-head">Simple - Secure - Scalable</h3>
<p class="abs body-copy modules-copy">Orvanta is the real estate industry's only infinitely composable Enterprise Applications Platform (EAP), ensuring scalability, security, auditability, and compliance. Orvanta is a complete solution covering all functional areas of real estate investment, development, finance, accounting, management and operations. No more business disruption, downtime, high costs, diminishing ROI, and inflexibility. Run your business your way, break the cycle of technical debt, and focus on high-value, innovative opportunities.</p>

<h2 class="abs platform-title h-mont">PLATFORM</h2>
<h3 class="abs pillar-title platform-head">Simple - Secure - Scalable</h3>
<p class="abs body-copy platform-copy">Orvanta combines the best of all worlds in our Enterprise Applications Platform (EAP): the simplicity and scalability of custom, no-code, software and the security and confidence of a complete, SOC 2 compliant industry solution. Our modular approach enables rapid innovation and re-invention of your business by casting off the shackles of legacy ERP technology and delivering a modern, agile solution that bridges the gaps for all of your real estate workflows. No more closed systems, complicated integrations, overreliance on spreadsheets, and complex or unavailable customizations. In their place is Orvanta's robust set of preconfigured yet flexible capabilities that can be deployed as point-solutions or to compose larger business processes.</p>
<div class="abs photo" style="left:676px;top:2447px;width:382px;height:438px;clip-path:polygon(50% 0,100% 25%,100% 75%,50% 100%,0 75%,0 25%);background:linear-gradient(160deg,#c9ccd2,#7a7f88 50%,#2d2f35)" role="img" aria-label="Hands on a laptop with floating ERP icons"></div>

<section class="about-us">
  <div class="abs brand"><span class="brand-square" style="width:60px;height:60px"></span>ORVANTA</div>
  <h2 class="abs h-mont">ABOUT <span>US</span></h2>
  <p class="abs body-copy">Orvanta is the real estate industry's modern alternative to rigid, legacy ERP systems. With decades of real estate enterprise software development and implementation expertise — spanning hundreds of blue chip global real estate investment firms — we have a proven track record of enterprise excellence.</p>
</section>

<footer class="site-footer">
  <div class="abs rule" style="top:3385px"></div>
  <div class="abs brand"><span class="brand-square"></span>ORVANTA</div>
  <div class="abs foot-col" style="left:445px;top:3436px"><h4>MENUS</h4><ul><li>Home</li><li>Market</li><li>Platform</li><li>Team</li></ul></div>
  <div class="abs foot-col" style="left:619px;top:3436px"><h4>LINKS</h4><ul><li>Terms of Use</li><li>Sitemap</li><li>Information</li><li>Schedule a demo</li></ul></div>
  <div class="abs foot-col" style="left:826px;top:3436px"><h4>SIGN UP NEWSLETTER</h4></div>
  <div class="abs newsletter"><span class="ph">Enter Email</span><span class="sub">SUBSCRIBE</span></div>
  <div class="abs rule" style="top:3620px"></div>
  <p class="abs copyright">Copyright © 2024 Orvanta. All Rights Reserved &nbsp;|&nbsp; Privacy &nbsp;|&nbsp; Terms of Use</p>
  <div class="abs social" aria-label="Social links"><span></span><span></span><span></span><span></span><span></span></div>
</footer>

</body>
</html>
```